Tech business card design

We need an amazing business card design for our new business 'Pexla' a marketing tech startup based in Sydney, Australia. We provide an online marketplace for businesses to search and buy advertising media, connect with service providers and learn more about marketing. We wish to communicate 'cool tech', reliability and professionalism and design based around our logo.

Target Market(s)

Business Owners

Contact Information for Business Card

Name
Position
Email Address
Website
Phone Number

Font styles to use
Other font styles liked:
• Avenir & Avenir Next

Colors

Designer to choose colors to be used in the design.

```html
<!DOCTYPE html>
<html lang="en">
<head>
<meta charset="UTF-8">
<title>Pexla Business Card</title>
<link href="https://fonts.googleapis.com/css2?family=Nunito+Sans:wght@400;700;900&display=swap" rel="stylesheet">
<style>
  :root {
    --navy: #141d4a;
    --navy-deep: #0f1640;
    --ink: #1b1f33;
    --muted: #8a8d99;
    --paper: #ffffff;
    --backdrop: #e6e7ea;
    --pattern-light: #f5f6f8;
    --pattern-mid: #eceef2;
  }
  * { margin: 0; padding: 0; box-sizing: border-box; }
  html, body { width: 1200px; height: 900px; overflow: hidden; }
  body {
    background: var(--backdrop);
    font-family: "Nunito Sans", "Avenir Next", Avenir, sans-serif;
    position: relative;
  }
  .card {
    position: absolute;
    width: 560px;
    height: 320px;
    border-radius: 4px;
    box-shadow: 0 10px 30px rgba(0,0,0,0.18);
    overflow: hidden;
  }
  .card-back {
    left: 90px;
    top: 100px;
    background: var(--navy-deep);
  }
  .card-back .pattern-area {
    position: absolute;
    inset: 0;
    background: linear-gradient(135deg, #18215a 0%, var(--navy-deep) 100%);
  }
  .card-back .wordmark {
    position: absolute;
    left: 0; right: 0;
    top: 50%;
    transform: translateY(-50%);
    text-align: center;
    color: var(--paper);
    font-weight: 900;
    font-size: 46px;
    letter-spacing: -1px;
  }
  .card-front {
    left: 550px;
    top: 480px;
    background: var(--paper);
  }
  .card-front .pattern-area {
    position: absolute;
    inset: 0;
    background: linear-gradient(100deg, var(--paper) 0%, var(--pattern-light) 40%, var(--pattern-mid) 100%);
  }
  .card-front .wordmark {
    position: absolute;
    left: 36px;
    top: 62px;
    color: var(--navy);
    font-weight: 900;
    font-size: 96px;
    line-height: 1;
    letter-spacing: -3px;
  }
  .contact {
    position: absolute;
    left: 36px;
    bottom: 30px;
  }
  .contact .person-name {
    color: var(--navy);
    font-weight: 900;
    font-size: 24px;
    line-height: 1.1;
  }
  .contact .person-role {
    color: var(--muted);
    font-size: 13px;
    margin-top: 2px;
  }
  .contact .details {
    color: var(--ink);
    font-size: 15px;
    margin-top: 10px;
    white-space: nowrap;
  }
  .contact .sep { color: var(--muted); padding: 0 5px; }
</style>
</head>
<body>
  <section class="card card-back">
    <div class="pattern-area" role="img" aria-label="Repeated brand name pattern in darker navy tones"></div>
    <div class="wordmark">Pexla</div>
  </section>

  <section class="card card-front">
    <div class="pattern-area" role="img" aria-label="Faint line-icon pattern of marketing tools: charts, gears, magnifiers, puzzle pieces and money"></div>
    <div class="wordmark">Pexla</div>
    <div class="contact">
      <p class="person-name">Marcus Lane</p>
      <p class="person-role">Managing Director</p>
      <p class="details">000-555-0192<span class="sep">|</span>info@pexlagmail.com<span class="sep">|</span>www.pexla.com</p>
    </div>
  </section>
</body>
</html>
```